Corporate Business Card

Very professional, Modern, Not to busy, include phone address email, website
(253) 617-4930, 18761 52nd Avenue S, Kent, WA 98047, martin@plumlinegroup.com, varkoworks.com

Target Market(s)

Manufacturing

Industry/Entity Type

Aero, machining, manufacturing, Off road racing

Contact Information for Business Card

Phone, address email, website

```html
<!DOCTYPE html>
<html lang="en">
<head>
<meta charset="utf-8">
<title>Varko Works – Business Card</title>
<link rel="stylesheet" href="https://fonts.googleapis.com/css2?family=Lato:wght@400;700;900&family=Michroma&display=swap">
<style>
  :root {
    --navy: #1e3065;
    --navy-light: #1a4a8a;
    --brand-blue: #1d3b7a;
    --brand-red: #d52329;
    --ink: #1c1c1c;
    --paper: #ffffff;
    --backdrop: #e9eaec;
  }
  * { box-sizing: border-box; margin: 0; padding: 0; }
  html, body { width: 1200px; height: 895px; overflow: hidden; }
  body {
    background: var(--backdrop);
    font-family: "Lato", Arial, sans-serif;
    display: flex;
    flex-direction: column;
    align-items: center;
    justify-content: center;
    gap: 30px;
  }
  .card {
    position: relative;
    width: 720px;
    height: 411px;
    overflow: hidden;
    box-shadow: 0 8px 24px rgba(0,0,0,0.18);
  }

  /* Front */
  .card-front {
    background: linear-gradient(115deg, var(--navy) 0%, var(--navy) 45%, var(--navy-light) 100%);
  }
  .logo {
    position: absolute;
    display: flex;
    align-items: center;
    gap: 14px;
    font-family: "Lato", Arial, sans-serif;
    font-weight: 900;
    letter-spacing: 1px;
    text-transform: uppercase;
  }
  .logo-square { width: 18px; height: 18px; background: var(--brand-red); }
  .card-front .logo {
    left: 50%; top: 50%;
    transform: translate(-50%, -60%);
    color: var(--paper);
    font-size: 56px;
  }
  .card-front .logo-rule {
    position: absolute;
    left: 200px; top: 248px;
    width: 170px; height: 2px;
    background: var(--paper);
  }

  /* Back */
  .card-back { background: var(--paper); }
  .card-back .logo {
    right: 48px; top: 44px;
    color: var(--brand-blue);
    font-size: 38px;
  }
  .card-back .logo-rule {
    position: absolute;
    right: 250px; top: 112px;
    width: 120px; height: 2px;
    background: var(--brand-blue);
  }
  .identity {
    position: absolute;
    left: 48px; top: 212px;
  }
  .person-name {
    font-family: "Michroma", "Arial Black", sans-serif;
    font-size: 25px;
    color: var(--brand-blue);
    letter-spacing: -0.5px;
  }
  .person-title {
    font-size: 17px;
    color: var(--ink);
    margin-top: 2px;
    display: flex;
    align-items: center;
    gap: 10px;
  }
  .divider {
    position: absolute;
    left: 236px; top: 257px;
    width: 440px; height: 1.5px;
    background: var(--ink);
  }
  .contact-list {
    position: absolute;
    left: 64px; top: 288px;
    list-style: none;
    font-size: 16px;
    color: var(--ink);
    line-height: 25px;
  }
  .contact-list li { display: flex; align-items: center; gap: 12px; }
  .contact-list svg { width: 15px; height: 15px; flex: none; }
  .address {
    position: absolute;
    left: 430px; top: 282px;
    font-size: 16px;
    color: var(--ink);
    line-height: 22px;
  }
  .base-band {
    position: absolute;
    left: 0; right: 0; bottom: 0;
    height: 8px;
    display: flex;
  }
  .base-band .band-blue { flex: 0 0 58%; background: var(--brand-blue); }
  .base-band .band-gap { flex: 0 0 6px; background: var(--paper); }
  .base-band .band-red { flex: 1; background: var(--brand-red); }
</style>
</head>
<body>

  <section class="card card-front">
    <div class="logo"><span class="logo-square"></span>Varko Works</div>
    <span class="logo-rule"></span>
  </section>

  <section class="card card-back">
    <div class="logo"><span class="logo-square"></span>Varko Works</div>
    <span class="logo-rule"></span>

    <div class="identity">
      <div class="person-name">MARTIN REYES</div>
      <div class="person-title">Founder &amp; CEO</div>
    </div>
    <span class="divider"></span>

    <ul class="contact-list">
      <li>
        <svg viewBox="0 0 24 24" aria-hidden="true"><path fill="var(--brand-red)" d="M6.6 10.8a15.1 15.1 0 0 0 6.6 6.6l2.2-2.2a1 1 0 0 1 1-.25 11.4 11.4 0 0 0 3.6.57 1 1 0 0 1 1 1V20a1 1 0 0 1-1 1A17 17 0 0 1 3 4a1 1 0 0 1 1-1h3.5a1 1 0 0 1 1 1c0 1.25.2 2.45.57 3.57a1 1 0 0 1-.25 1z"/></svg>
        (253) 617-4930
      </li>
      <li>
        <svg viewBox="0 0 24 24" aria-hidden="true"><rect x="2.5" y="5" width="19" height="14" fill="none" stroke="var(--brand-red)" stroke-width="2.2"/><path d="M3 6l9 7 9-7" fill="none" stroke="var(--brand-red)" stroke-width="2.2"/></svg>
        martin@plumlinegroup.com
      </li>
      <li>
        <svg viewBox="0 0 24 24" aria-hidden="true"><g fill="none" stroke="var(--brand-red)" stroke-width="2"><circle cx="12" cy="12" r="9.5"/><ellipse cx="12" cy="12" rx="4.2" ry="9.5"/><path d="M2.5 12h19M4 7h16M4 17h16"/></g></svg>
        varkoworks.com
      </li>
    </ul>

    <address class="address" style="font-style:normal">
      18761 52nd Avenue S, Kent<br>WA 98047
    </address>

    <div class="base-band"><span class="band-blue"></span><span class="band-gap"></span><span class="band-red"></span></div>
  </section>

</body>
</html>
```